Brindle Asset Management Vendor Recruiting Email

We need a digital flyer to email and post on Social media to attract new vendors to our website to apply to complete maintenance work on our clients homes. I have one flyer we had produced recently that we are un-happy with. It is attached.

The example given is what we do not want!! We do not want any of the pictures used from the existing one

Target Market(s)

Construction companies and handyman

Industry/Entity Type

Residential maintenance and repairs

Requirements
Must have
• Join our team as the header not become a vendor

```html
<!DOCTYPE html>
<html lang="en">
<head>
<meta charset="utf-8">
<title>Brindle Asset Management – Join Our Team</title>
<link rel="stylesheet" href="https://fonts.googleapis.com/css2?family=Great+Vibes&family=Montserrat:wght@700&family=PT+Sans:ital,wght@0,400;1,700&family=Roboto+Condensed:wght@300;700&family=Bowlby+One&display=swap">
<style>
  :root {
    --frame-purple: #654b7d;
    --brand-purple: #6b2c94;
    --brand-violet: #8a3fb8;
    --ink: #1c1c1c;
    --card-glass: rgba(246, 244, 248, 0.8);
    --sky-top: #8fb8de;
    --sky-mid: #d6e6f4;
    --grass: #6a9a3a;
    --workwear: #2d3a5c;
    --logo-black: #0d0c14;
    --white: #ffffff;
    --page-bg: #ffffff;
  }
  * { margin: 0; padding: 0; box-sizing: border-box; }
  html, body {
    width: 1200px; height: 1200px; overflow: hidden;
    background: var(--page-bg);
  }
  .flyer {
    position: absolute; left: 40px; top: 183px;
    width: 1120px; height: 834px;
    background: var(--frame-purple);
    overflow: hidden;
  }
  .photo-panel {
    position: absolute; left: 41px; top: 37px;
    width: 1035px; height: 735px;
    border: 3px solid var(--white);
    border-radius: 30px;
    overflow: hidden;
    background:
      linear-gradient(90deg, var(--workwear) 0%, rgba(45,58,92,0.85) 28%, rgba(45,58,92,0) 46%),
      linear-gradient(180deg, var(--sky-top) 0%, var(--sky-mid) 45%, #e9eef2 70%, #9cbf6a 86%, var(--grass) 100%);
  }
  .headline-script {
    position: absolute; right: 80px; top: 86px;
    font: 400 74px/1 "Great Vibes", cursive;
    color: var(--ink);
    white-space: nowrap;
  }
  .headline-main {
    position: absolute; right: 68px; top: 174px;
    font: 700 88px/1 "Montserrat", sans-serif;
    letter-spacing: 1px;
    white-space: nowrap;
    background: linear-gradient(90deg, var(--brand-purple), var(--brand-violet));
    -webkit-background-clip: text; background-clip: text;
    color: transparent;
  }
  .info-card {
    position: absolute; top: 309px; height: 425px;
    background: var(--card-glass);
    box-shadow: 0 2px 6px rgba(0,0,0,0.15);
  }
  .benefits-card { left: 77px; width: 487px; border-radius: 0 22px 22px 0; }
  .requirements-card { left: 590px; width: 443px; border-radius: 28px 28px 0 0; }
  .bullet-list { list-style: none; position: absolute; left: 0; top: 0; width: 100%; }
  .bullet-list li {
    position: absolute; left: 0;
    font: 400 21.5px/22px "PT Sans", sans-serif;
    color: var(--ink);
    white-space: nowrap;
  }
  .bullet-list li::before {
    content: ""; position: absolute; top: 5px;
    width: 9px; height: 9px; border-radius: 50%;
    background: var(--brand-purple);
  }
  .bullet-list li.continued::before { display: none; }
  .benefits-card li { padding-left: 46px; }
  .benefits-card li::before { left: 21px; }
  .requirements-card li { padding-left: 58px; line-height: 26px; }
  .requirements-card li::before { left: 29px; top: 9px; }
  .requirements-heading {
    position: absolute; left: 27px; top: 26px;
    font: 400 30px/37px "Bowlby One", sans-serif;
    color: var(--brand-purple);
    text-shadow: 0 0 2px var(--white), 1px 1px 0 var(--white), -1px -1px 0 var(--white);
    letter-spacing: -0.5px;
    white-space: nowrap;
  }
  .call-block { position: absolute; left: 41px; top: 320px; }
  .call-icon { position: absolute; left: 0; top: 0; width: 58px; height: 75px; }
  .call-label {
    position: absolute; left: 71px; top: 0; white-space: nowrap;
    font: 300 28px/1 "Roboto Condensed", sans-serif;
    color: var(--brand-violet);
  }
  .call-number {
    position: absolute; left: 69px; top: 28px; white-space: nowrap;
    font: 700 52px/1 "Roboto Condensed", sans-serif;
    color: var(--brand-purple);
    letter-spacing: -1px;
  }
  .website {
    position: absolute; left: 71px; top: 786px;
    display: flex; align-items: center; gap: 10px;
    font: italic 700 29px/1 "PT Sans", sans-serif;
    color: var(--white);
    white-space: nowrap;
  }
  .website svg { width: 29px; height: 29px; }
  .brand-block {
    position: absolute; left: 742px; top: 710px;
    width: 218px; height: 124px;
    background: var(--logo-black);
    border-radius: 19px 19px 0 0;
    display: flex; flex-direction: column; align-items: center; justify-content: center;
    color: var(--white);
    font-family: "Montserrat", sans-serif; font-weight: 700;
    text-align: center;
  }
  .brand-name { font-size: 21px; letter-spacing: 3px; line-height: 1.1; }
  .brand-sub { font-size: 7.5px; letter-spacing: 1.5px; margin-top: 4px; }
</style>
</head>
<body>
  <main class="flyer">
    <div class="photo-panel" role="img" aria-label="Photo of a tradesman in navy work overalls with a yellow tool belt, writing on a blue clipboard, in front of a house, green lawn and blue sky"></div>

    <div class="headline-script">Join our</div>
    <h1 class="headline-main">TEAM</h1>

    <section class="info-card benefits-card">
      <ul class="bullet-list">
        <li style="top:40px">95% approval rating on all submitted<br>estimates.</li>
        <li style="top:107px">Guaranteed work volume.</li>
        <li style="top:151px">Material purchasing program to help vendors<br>with low capital or no or bad credit.</li>
        <li style="top:218px">Weekly secure direct deposit with net 30<br>payment terms.</li>
      </ul>
      <div class="call-block">
        <svg class="call-icon" viewBox="0 0 58 75" aria-hidden="true">
          <rect x="4" y="0" width="54" height="75" rx="4" fill="var(--brand-purple)"/>
          <rect x="0" y="10" width="8" height="4" rx="2" fill="var(--brand-purple)"/>
          <rect x="0" y="24" width="8" height="4" rx="2" fill="var(--brand-purple)"/>
          <rect x="0" y="38" width="8" height="4" rx="2" fill="var(--brand-purple)"/>
          <rect x="0" y="52" width="8" height="4" rx="2" fill="var(--brand-purple)"/>
          <rect x="46" y="4" width="4" height="67" fill="#fff"/>
          <path d="M20 18c3-2 6-2 7 1l3 8c1 2 0 4-2 5l-2 1c1 5 4 10 8 13l2-1c2-1 4-1 5 1l4 7c1 2 0 4-2 5-3 2-7 3-10 1-9-5-15-15-17-26-1-6 1-12 4-15z" fill="#fff"/>
        </svg>
        <div class="call-label">More information call us</div>
        <div class="call-number">731-555-0186</div>
      </div>
    </section>

    <section class="info-card requirements-card">
      <h2 class="requirements-heading">REQUIREMENTS TO<br>BECOME A VENDOR</h2>
      <ul class="bullet-list">
        <li style="top:119px">Auto insurance</li>
        <li style="top:157px">Certificate of general liability insurance</li>
        <li style="top:194px">Workman’s Compensation or state</li>
        <li class="continued" style="top:232px">issued exemption letter</li>
        <li style="top:269px">Drive License or state issued ID card</li>
        <li style="top:307px">Coverage area</li>
        <li style="top:344px">Any speciality Licenses</li>
      </ul>
    </section>

    <div class="website">
      <svg viewBox="0 0 30 30" aria-hidden="true" fill="none" stroke="#fff" stroke-width="2">
        <circle cx="15" cy="15" r="13"/>
        <ellipse cx="15" cy="15" rx="6" ry="13"/>
        <line x1="2" y1="15" x2="28" y2="15"/>
        <line x1="4" y1="8" x2="26" y2="8"/>
        <line x1="4" y1="22" x2="26" y2="22"/>
      </svg>
      <span>www.brindleassetmanagement.com</span>
    </div>

    <div class="brand-block">
      <span class="brand-name">BRINDLE</span>
      <span class="brand-sub">ASSET MANAGEMENT</span>
    </div>
  </main>
</body>
</html>
```